Non Profit Company Looking For New Website

The website for Fernvale Quillstone Heritage Society should offer the viewer beautiful photos that inspire condifence and joy and tap into our love of horses.

We would like to see a website that displays trust, quality and confidence. Needs to be responsive and mobile friendly for all browsers and coded for both Android & IOS.

READ ATTACHED WEBSITE TEMPLATE FOR COMPLETE DETAILS ON WHAT WE ARE LOOKING FOR.

Looking for recommmendations if we should use WordPress/WooCommerce for site or Wordpress with Shopify Plug in or just Shopify.

Must be both desktop and mobile friendly with fast page load speed. Need the ability to edit ourselves.

Industry/Entity Type

Non Profit

Coding

Coded - Design and coding required

Number of Pages Required

5+ page

Requirements
Must have
• We would like to see a website that displays trust, quality and confidence. Needs to be responsive and mobile friendly for all browsers and coded for both Android & IOS.

Looking for recommendations if we should use WordPress/WooCommerce for site or Wordpress with Shopify Plug in or just Shopify.

Logo Colour:
Pantone 7621 C

READ TEMPLATE THAT IS ATTACHED
Nice to have
• Like look of this website as a sample:
https://www.quellbrimtorva.com/

Another similar non profit organization
https://pellaworthcindle.com/

```html
<!DOCTYPE html>
<html lang="en">
<head>
<meta charset="utf-8">
<title>Fernvale Quillstone Heritage Society</title>
<link href="https://fonts.googleapis.com/css2?family=Lato:wght@400;700;900&display=swap" rel="stylesheet">
<style>
:root{
  --red:#b8202e;
  --ink:#2b2b2b;
  --muted:#555;
  --lavender:#ebebf3;
  --white:#fff;
  --black:#000;
}
*{box-sizing:border-box;margin:0;padding:0}
html,body{width:1200px;height:3397px;overflow:hidden}
body{position:relative;font-family:'Lato',sans-serif;color:var(--ink);background:var(--white)}
.abs{position:absolute}
.btn{position:absolute;display:flex;align-items:center;justify-content:center;color:var(--white);font-weight:700;text-transform:uppercase;background:var(--red);box-shadow:0 3px 6px rgba(0,0,0,.2)}

/* header */
.site-header{left:0;top:0;width:1200px;height:123px;background:var(--white);border-bottom:1px solid #ddd}
.brand{left:112px;top:22px;width:130px;display:flex;flex-direction:column;align-items:center;gap:4px;color:var(--red);font-weight:700;text-align:center;font-size:13px;line-height:1.15;text-transform:uppercase}
.brand-mark{width:18px;height:18px;background:var(--red);border-radius:50%}
.btn-adopt{left:762px;top:16px;width:154px;height:44px;background:var(--black);font-size:15px}
.btn-donate{left:932px;top:16px;width:154px;height:44px;font-size:15px}
.main-nav{right:114px;top:85px;display:flex;gap:24px;font-size:15px}
.main-nav a{color:var(--ink);text-decoration:none}
.main-nav a.active{color:var(--red)}

/* hero */
.hero{left:0;top:123px;width:1200px;height:643px;background:linear-gradient(180deg,#4a5f73 0%,#55663a 30%,#3f5a24 60%,#4d6a2a 100%)}
.hero-horse{left:640px;top:123px;width:380px;height:643px;background:radial-gradient(ellipse at 50% 55%,#8b5a2b 0%,#5a3a1d 55%,transparent 75%)}
.hero-kicker{left:112px;top:345px;width:520px;color:var(--white);font-weight:700;font-size:16px;line-height:29px}
.hero-title{left:112px;top:402px;color:var(--white);font-weight:700;font-size:44px;letter-spacing:.5px}
.hero-text{left:112px;top:465px;width:520px;color:var(--white);font-size:15px;line-height:29px}

/* about */
.about{left:0;top:766px;width:1200px;height:540px;background:var(--lavender)}
.about-photo{left:120px;top:835px;width:430px;height:430px;border-radius:50%;border:3px solid var(--white);box-shadow:0 6px 14px rgba(0,0,0,.25);background:radial-gradient(circle at 40% 40%,#a4623a 0%,#7f4526 45%,#9fb6cc 75%,#d7e1ea 100%)}
.about-title{left:600px;top:905px;font-size:32px;font-weight:700;color:var(--ink)}
.about-text{left:600px;top:964px;width:490px;font-size:13px;line-height:27.5px;color:var(--muted)}
.about-text p+p{margin-top:11px}
.btn-learn{left:600px;top:1135px;width:209px;height:52px;font-size:13px}

/* adopt */
.adopt-title{left:0;top:1358px;width:1200px;text-align:center;font-size:42px;font-weight:700}
.horse-grid{left:112px;top:1440px;width:976px;display:grid;grid-template-columns:repeat(3,318px);grid-auto-rows:274px;gap:9px 11px}
.horse-card{position:relative;box-shadow:0 2px 5px rgba(0,0,0,.2)}
.horse-card.featured{border:5px solid var(--white);box-shadow:0 2px 8px rgba(0,0,0,.3)}
.h1{background:linear-gradient(135deg,#b5744a,#6e3d22 60%,#c48a5a)}
.h2{background:linear-gradient(180deg,#5f6f86 0%,#7b7a55 45%,#5e7a2e 100%)}
.h3{background:linear-gradient(90deg,#6f7d5b,#2b2a26 55%,#7c8a68)}
.h4{background:linear-gradient(180deg,#e7e2dc 0%,#c9b8a2 45%,#5d6b3a 75%,#46592b 100%)}
.h5{background:linear-gradient(180deg,#7fa9d8 0%,#c4d6e6 40%,#c98a47 70%,#5b4631 100%)}
.h6{background:linear-gradient(135deg,#3e5a2c,#8a4a26 50%,#5d7a3a)}
.card-btn{left:82px;top:108px;width:154px;height:44px;font-size:15px}

/* difference */
.difference{left:0;top:2083px;width:1200px;height:558px;background:linear-gradient(100deg,#8a5a1c 0%,#5a3512 40%,#2e1c0c 75%,#3a2410 100%)}
.diff-title{left:112px;top:2205px;color:var(--white);font-size:58px;font-weight:700}
.diff-text{left:112px;top:2286px;width:470px;color:var(--white);font-size:15px;line-height:30px}
.btn-give{left:112px;top:2395px;width:208px;height:52px;font-size:13px}

/* contact */
.contact{left:0;top:2641px;width:1200px;height:624px;background:var(--lavender)}
.line-top{left:0;top:2726px;width:415px;height:24px;border-top:1px solid var(--red);border-right:1px solid var(--red)}
.line-left{left:0;top:3195px;width:113px;border-top:1px solid var(--red)}
.contact-form{left:113px;top:2751px;width:442px;height:553px;background:var(--white);box-shadow:0 2px 8px rgba(0,0,0,.12);padding:61px 29px 0}
.field{display:block;width:385px;height:51px;border:1px solid #ccc;margin-bottom:17px;padding:0 10px;font:14px 'Lato',sans-serif;color:#444;display:flex;align-items:center}
.field.message{height:84px;align-items:flex-start;padding-top:14px;margin-bottom:34px}
.btn-submit{position:static;width:385px;height:50px;font-size:17px;box-shadow:none}
.contact-title{left:619px;top:2780px;font-size:42px;font-weight:700}
.contact-text{left:619px;top:2837px;width:480px;font-size:15px;line-height:29px;color:var(--ink)}
.info-card{left:619px;top:2937px;width:469px;height:276px;background:var(--white);box-shadow:0 2px 8px rgba(0,0,0,.12);padding:50px 22px 0}
.info-card h3{font-size:21px;font-weight:700;margin-bottom:22px}
.info-row{font-size:15px;line-height:31px;margin-bottom:6px;color:var(--ink)}
.info-row .lbl{color:var(--red)}
.info-row svg{width:13px;height:13px;vertical-align:-1px;fill:var(--red);margin-right:4px}

/* footer */
.site-footer{left:0;top:3265px;width:1200px;height:132px;background:var(--red)}
.copyright{left:0;top:3342px;width:1200px;text-align:center;color:var(--white);font-size:18px}
</style>
</head>
<body>

<header class="abs site-header">
  <div class="abs brand"><span class="brand-mark"></span>Fernvale Quillstone<br>Heritage Society</div>
  <div class="btn btn-adopt">Adopt Now</div>
  <div class="btn btn-donate">Donate Now</div>
  <nav class="abs main-nav">
    <a class="active" href="#">Home</a>
    <a href="#">About</a>
    <a href="#">What is Thoroughbred Aftercare?</a>
    <a href="#">Adopt a Horse</a>
    <a href="#">Contact</a>
  </nav>
</header>

<section class="abs hero" role="img" aria-label="Photo of horses grazing in a green meadow with a bay horse in the foreground"></section>
<div class="abs hero-horse" role="img" aria-label="Bay horse standing in the meadow"></div>
<p class="abs hero-kicker">We support and develop retired thoroughbred race horses for their next chapter in life</p>
<h1 class="abs hero-title">RETIRE. RETRAIN. REHOME.</h1>
<p class="abs hero-text">Fernvale Quillstone Heritage Society (FQHS) is a registered not-for-profit organization in Fernvale.</p>

<section class="abs about"></section>
<div class="abs about-photo" role="img" aria-label="Circular photo of a chestnut horse with flowing mane"></div>
<h2 class="abs about-title">What is Thoroughbred Aftercare?</h2>
<div class="abs about-text">
  <p>The health, safety and welfare of our equine athletes does not end at the finish line, and retirement and aftercare are critical to the success of the racing industry.</p>
  <p>Aftercare is the safe placement of racehorses after their careers as racehorse are completed. Some horses might retire to the breeding shed or broodmare bands, while others are retrained for second careers.</p>
</div>
<div class="btn btn-learn">Learn More About Us</div>

<h2 class="abs adopt-title">Adopt a Horse</h2>
<div class="abs horse-grid">
  <div class="horse-card h1" role="img" aria-label="Photo of a bay horse in a halter among autumn trees"></div>
  <div class="horse-card h2 featured" role="img" aria-label="Photo of a chestnut horse on open prairie">
    <div class="btn card-btn">Adopt Now</div>
  </div>
  <div class="horse-card h3" role="img" aria-label="Photo of a black horse with a white blaze"></div>
  <div class="horse-card h4" role="img" aria-label="Photo of a horse standing in a field at dusk"></div>
  <div class="horse-card h5" role="img" aria-label="Photo of a palomino horse looking over a fence"></div>
  <div class="horse-card h6" role="img" aria-label="Photo of a bay horse galloping on grass"></div>
</div>

<section class="abs difference" role="img" aria-label="Photo of horses running at sunset through golden dust"></section>
<h2 class="abs diff-title">Make a Difference</h2>
<p class="abs diff-text">Lorem ipsum dolor sit amet, consectetur adipiscing elit, sed do eiusmod tempor incididunt ut labore et dolore magna aliqua. Ut enim ad minim veniam, quis nostrud</p>
<div class="btn btn-give">More Ways to Give</div>

<section class="abs contact"></section>
<div class="abs line-top"></div>
<div class="abs line-left"></div>
<form class="abs contact-form">
  <div class="field">Name</div>
  <div class="field">Email</div>
  <div class="field">Phone</div>
  <div class="field">Address</div>
  <div class="field message">Message</div>
  <div class="btn btn-submit">Submit</div>
</form>
<h2 class="abs contact-title">Contact Us</h2>
<p class="abs contact-text">Lorem ipsum dolor sit amet, consectetur adipiscing elit, sed do eiusmod tempor incididunt ut labore et dolore magna</p>
<div class="abs info-card">
  <h3>For more information</h3>
  <p class="info-row"><svg viewBox="0 0 16 16"><path d="M3.6 1.2l2.4 2.6-1.3 2a9 9 0 0 0 5.5 5.5l2-1.3 2.6 2.4-1.5 2.1C7 14.5 1.5 9 1.5 2.7z"/></svg><span class="lbl">Phone:</span> 123-456-7890</p>
  <p class="info-row"><svg viewBox="0 0 16 16"><path d="M1 3h14v10H1z M1 3l7 6 7-6" stroke="#fff" stroke-width="1.2"/></svg><span class="lbl">Email:</span> FernvaleQuillstone.org</p>
  <p class="info-row"><svg viewBox="0 0 16 16"><path d="M1 3h14v10H1z M1 3l7 6 7-6" stroke="#fff" stroke-width="1.2"/></svg><span class="lbl">Address:</span> 123,Lorem ipsum dolor sit amet, consectetur adipiscing elit,</p>
</div>

<footer class="abs site-footer"></footer>
<p class="abs copyright">© 2021 All Rights Reserved</p>

</body>
</html>
```